Vale Linebacker Needs a new website!

We need a four page website for a new company based in San Francisco. We help companies connect better with their clients, employees, and vendors by implementing collaborative technology.
Similar Websites
Mist Rangers - http://www.mistrangers.example/
Skyforthing - http://www.skyforthing.example/ - I don't like the the rotating window or the pictures of people. I like the icons used to go to the next pages.
Color Combos
Blues and Yellows - http://www.huepairings.example/palette-sets/96/HuePairing96.html
We prefer graphics over the actual pictures of people in the header. Pictures of people working together in the text is fine.
Web Page Layout
Index
Cloud Advisory Services
Email Everywhere
CRM Implementation
For detailed copy please see this link https://files.paperhold.example/a/widgetladyla.example/document/d/7KtmPzWqAeRbYcNvHsJgLdFxTuQoIeMnBvCxZaSdFgHj/edit
Industry/Entity Type
It Company

```html
<!DOCTYPE html>
<html lang="en">
<head>
<meta charset="utf-8">
<title>Vale Linebacker</title>
<link rel="stylesheet" href="https://fonts.googleapis.com/css2?family=Open+Sans:ital,wght@0,300;0,400;0,600;0,700;1,400;1,700&family=Arimo:ital,wght@0,400;0,700;1,400;1,700&display=swap">
<style>
:root{
  --ink-dark:#1a1a1a;
  --footer:#1e2021;
  --footer-base:#141515;
  --brand-blue:#2866b2;
  --heading-blue:#2a68b3;
  --gold:#d6a90b;
  --gold-edge:#b08a06;
  --mist:#dcdcdc;
  --text-grey:#555a5e;
  --muted:#9a9ea2;
  --white:#ffffff;
}
*{margin:0;padding:0;box-sizing:border-box}
html,body{width:1200px;height:2400px;overflow:hidden;background:var(--white)}
body{position:relative;font-family:"Arimo",Arial,sans-serif;color:var(--text-grey)}
.abs{position:absolute}
.center-text{text-align:center;left:0;width:1200px}

/* header */
.site-header{position:absolute;left:0;top:0;width:1200px;height:82px;background:var(--ink-dark)}
.brand{position:absolute;left:173px;top:27px;display:flex;align-items:center;gap:10px}
.brand-dot{width:26px;height:26px;border-radius:50%;background:var(--brand-blue)}
.brand-name{font-family:"Open Sans",sans-serif;font-weight:700;font-size:22px;color:var(--white)}
.main-nav a{position:absolute;top:34px;font-family:"Arimo",sans-serif;font-size:13px;color:#d6d6d6;text-decoration:none;white-space:nowrap}

/* hero */
.hero{position:absolute;left:0;top:82px;width:1200px;height:532px;overflow:hidden}
.hero-photo{position:absolute;inset:0;background:linear-gradient(160deg,#7d858c 0%,#5a6168 35%,#3d434a 70%,#2b3036 100%)}
.hero-shade{position:absolute;inset:0;background:rgba(20,24,30,.25)}
.slide-arrow{position:absolute;top:226px}
.hero-title{position:absolute;top:258px;font-family:"Open Sans",sans-serif;font-weight:300;font-size:48px;color:var(--white)}
.hero-sub{position:absolute;top:328px;font-family:"Open Sans",sans-serif;font-weight:300;font-size:29px;color:var(--white)}
.btn-gold{position:absolute;left:514px;width:171px;height:44px;background:var(--gold);border-bottom:3px solid var(--gold-edge);color:var(--white);font-family:"Arimo",sans-serif;font-size:13px;text-align:center;line-height:42px;text-transform:uppercase}

/* services */
.section-title{position:absolute;font-family:"Open Sans",sans-serif;font-weight:400;font-size:38px;color:var(--heading-blue)}
.services-sub{position:absolute;top:724px;font-size:15px;color:#555}
.service{position:absolute;top:797px;width:220px;text-align:center}
.service-icon{display:block;margin:0 auto}
.service h3{margin-top:14px;font-family:"Open Sans",sans-serif;font-weight:400;font-size:16px;color:var(--heading-blue)}
.service p{margin-top:8px;font-size:11.5px;line-height:20px;color:#666}

/* what we do */
.what-band{position:absolute;left:0;top:1024px;width:1200px;height:256px;background:var(--mist)}
.what-copy{position:absolute;left:230px;top:1116px;width:740px;font-size:15.5px;line-height:27px;text-align:center;color:#55595d}

/* offerings */
.offer{position:absolute;top:1336px;width:272px;text-align:center}
.offer-image{width:272px;height:176px}
.offer h3{margin-top:14px;font-family:"Open Sans",sans-serif;font-weight:400;font-size:18px;color:var(--heading-blue)}
.offer p{margin-top:10px;font-size:12.5px;line-height:21px;color:#444}

/* testimonials */
.testimonials{position:absolute;left:0;top:1693px;width:1200px;height:379px;background:var(--brand-blue)}
.testimonials-title{position:absolute;top:1728px;font-family:"Open Sans",sans-serif;font-weight:300;font-size:40px;color:var(--white)}
.client-portrait{position:absolute;left:199px;top:1815px;width:198px;height:198px;border-radius:50%;background:radial-gradient(circle at 50% 40%,#e8ecef 0%,#b7c1c9 55%,#3b4550 100%);border:4px solid var(--white)}
.quote-text{position:absolute;left:486px;top:1830px;width:490px;font-style:italic;font-size:13px;line-height:25.6px;color:var(--white)}
.quote-mark{position:absolute;font-family:"Open Sans",sans-serif;font-weight:700;font-size:40px;color:#cfd9e8;line-height:1}
.quote-name{position:absolute;left:486px;top:1949px;font-size:14px;color:var(--white)}
.quote-meta{position:absolute;left:486px;font-size:11px;font-weight:700;font-style:italic;color:var(--white)}

/* footer */
.site-footer{position:absolute;left:0;top:2072px;width:1200px;height:250px;background:var(--footer)}
.footer-col{position:absolute;top:2112px}
.footer-col h4{font-family:"Arimo",sans-serif;font-weight:400;font-size:14.5px;color:#e6e6e6;padding-bottom:9px;border-bottom:1px solid #55595c}
.footer-col ul{list-style:none;margin-top:10px}
.footer-col li{font-size:11.5px;line-height:24.8px;color:#9a9ea2;white-space:nowrap}
.footer-base{position:absolute;left:0;top:2322px;width:1200px;height:78px;background:var(--footer-base)}
.copyright{position:absolute;left:174px;top:2352px;font-size:11px;color:#8c8f92}
.social{position:absolute;top:2344px;width:28px;height:28px;border-radius:50%;background:#5a5d60}
</style>
</head>
<body>

<header class="site-header">
  <div class="brand"><span class="brand-dot"></span><span class="brand-name">Vale Linebacker</span></div>
  <nav class="main-nav">
    <a style="left:515px">Home</a>
    <a style="left:610px">About us</a>
    <a style="left:722px">Services</a>
    <a style="left:830px">What We Do</a>
    <a style="left:962px">Contact us</a>
  </nav>
</header>

<section class="hero">
  <div class="hero-photo" role="img" aria-label="Hands holding a white tablet over a desk"></div>
  <div class="hero-shade"></div>
  <svg class="slide-arrow" style="left:59px" width="52" height="52" viewBox="0 0 52 52"><circle cx="26" cy="26" r="24" fill="none" stroke="#8c9196" stroke-width="2"/><path d="M30 15 L18 26 L30 37 Z" fill="#8c9196"/></svg>
  <svg class="slide-arrow" style="left:1088px" width="52" height="52" viewBox="0 0 52 52"><circle cx="26" cy="26" r="24" fill="none" stroke="#8c9196" stroke-width="2"/><path d="M22 15 L34 26 L22 37 Z" fill="#8c9196"/></svg>
  <h1 class="hero-title center-text">Universal Access</h1>
  <p class="hero-sub center-text">Success in the cloud begins with a sound strategy.</p>
  <div class="btn-gold" style="top:400px">Read more info</div>
</section>

<h2 class="section-title center-text" style="top:660px">Our services include</h2>
<p class="services-sub center-text">Evaluation of current infrastructure and comparison of Gridline Suite and Deskwork 365</p>

<div class="service" style="left:157px">
  <svg class="service-icon" width="80" height="80" viewBox="0 0 80 80"><circle cx="40" cy="40" r="40" fill="var(--brand-blue)"/><rect x="20" y="28" width="24" height="18" rx="2" fill="none" stroke="#fff" stroke-width="2.5"/><path d="M16 50 H48" stroke="#fff" stroke-width="2.5"/><rect x="50" y="24" width="10" height="7" fill="none" stroke="#fff" stroke-width="2"/><rect x="50" y="36" width="10" height="7" fill="none" stroke="#fff" stroke-width="2"/><rect x="50" y="48" width="10" height="7" fill="none" stroke="#fff" stroke-width="2"/></svg>
  <h3>Deployment</h3>
  <p>Vale Linebacker has years of<br>experience in providing cloud com-<br>puting and strategic...</p>
</div>
<div class="service" style="left:386px">
  <svg class="service-icon" width="80" height="80" viewBox="0 0 80 80"><circle cx="40" cy="40" r="40" fill="var(--brand-blue)"/><circle cx="40" cy="40" r="19" fill="none" stroke="#fff" stroke-width="3" stroke-dasharray="90 30"/><path d="M30 44 a6 6 0 0 1 2-11 a8 8 0 0 1 15 1 a5 5 0 0 1 2 10 Z" fill="#fff"/></svg>
  <h3>Migration</h3>
  <p>Vale Linebacker has years of<br>experience in providing cloud com-<br>puting and strategic...</p>
</div>
<div class="service" style="left:602px">
  <svg class="service-icon" width="80" height="80" viewBox="0 0 80 80"><circle cx="40" cy="40" r="40" fill="var(--brand-blue)"/><rect x="25" y="20" width="30" height="40" rx="2" fill="none" stroke="#fff" stroke-width="2.5"/><circle cx="33" cy="32" r="3" fill="#fff"/><circle cx="47" cy="32" r="3" fill="#fff"/><circle cx="40" cy="46" r="3" fill="#fff"/><path d="M33 32 L40 46 L47 32" stroke="#fff" stroke-width="1.5" fill="none"/></svg>
  <h3>Project management</h3>
  <p>Vale Linebacker has years of<br>experience in providing cloud com-<br>puting and strategic...</p>
</div>
<div class="service" style="left:828px">
  <svg class="service-icon" width="80" height="80" viewBox="0 0 80 80"><circle cx="40" cy="40" r="40" fill="var(--brand-blue)"/><path d="M20 40 L40 48 L60 40 L60 56 L40 62 L20 56 Z" fill="#fff"/><circle cx="40" cy="31" r="7" fill="#fff"/></svg>
  <h3>Training</h3>
  <p>Vale Linebacker has years of<br>experience in providing cloud com-<br>puting and strategic...</p>
</div>

<div class="what-band"></div>
<h2 class="section-title center-text" style="top:1056px">What we do</h2>
<p class="what-copy">We challenge the status quo by providing unique insights, emerging strategies and proven best practices. Our unwavering focus is on customer satisfaction.&nbsp; Our services include:</p>
<div class="btn-gold" style="top:1194px">Read more info</div>

<article class="offer" style="left:171px">
  <div class="offer-image" role="img" aria-label="Open hand with floating device icons on a light background" style="background:linear-gradient(180deg,#f2f2f2,#d8d8d8)"></div>
  <h3>Cloud Advisory</h3>
  <p>Forward- thinking organizations would like to<br>be more collaborative, flexible and productive.<br>Put your cloud program on the path to success<br>with our Advisory Services.</p>
</article>
<article class="offer" style="left:464px">
  <div class="offer-image" role="img" aria-label="Finger touching an email envelope with a green at-sign" style="background:radial-gradient(circle at 50% 40%,#9aa3a8,#3e464c 80%)"></div>
  <h3>Email Everywhere</h3>
  <p>Forward- thinking organizations would like to<br>be more collaborative, flexible and productive.<br>Put your cloud program on the path to success<br>with our Advisory Services.</p>
</article>
<article class="offer" style="left:757px">
  <div class="offer-image" role="img" aria-label="Person in a shirt holding a tablet showing cloud graphics" style="background:linear-gradient(90deg,#2a3238,#8a9094 50%,#2a3238)"></div>
  <h3>CRM Solutions</h3>
  <p>Forward- thinking organizations would like to<br>be more collaborative, flexible and productive.<br>Put your cloud program on the path to success<br>with our Advisory Services.</p>
</article>

<section class="testimonials"></section>
<h2 class="testimonials-title center-text">Testimonials</h2>
<svg class="abs" style="left:143px;top:1898px" width="16" height="28" viewBox="0 0 16 28"><path d="M12 2 L4 14 L12 26" fill="none" stroke="#c5d3e8" stroke-width="2"/></svg>
<svg class="abs" style="left:1043px;top:1898px" width="16" height="28" viewBox="0 0 16 28"><path d="M4 2 L12 14 L4 26" fill="none" stroke="#c5d3e8" stroke-width="2"/></svg>
<div class="client-portrait" role="img" aria-label="Portrait of the client in a dark suit"></div>
<span class="quote-mark" style="left:452px;top:1806px">&ldquo;</span>
<p class="quote-text">IT services consultant and infrastructure architect with a strong background in a wide range of IT infrastructure and application development exposure. Most effective designing and managing infrastructure and IT services in startups, high tech companies, and companies undergoing growth and structural change.</p>
<span class="quote-mark" style="left:974px;top:1912px">&rdquo;</span>
<p class="quote-name">JR Halden</p>
<p class="quote-meta" style="top:1973px">Vale Linebacker Web Requirements</p>
<p class="quote-meta" style="top:1993px">May 22,2014</p>

<footer class="site-footer"></footer>
<div class="footer-col" style="left:174px;width:133px">
  <h4>Welcome</h4>
  <ul><li>Home</li><li>About us</li><li>Services</li><li>What We Do</li><li>Contact us</li></ul>
</div>
<div class="footer-col" style="left:370px;width:194px">
  <h4>What We Do</h4>
  <ul><li>Strategy</li><li>Migration</li><li>Implementation</li><li>Integration</li><li>Adoption and change management</li></ul>
</div>
<div class="footer-col" style="left:627px;width:194px">
  <h4>Services</h4>
  <ul><li>Deployment</li><li>Migration</li><li>User adoption and change management</li><li>Project management</li><li>Training</li></ul>
</div>
<div class="footer-col" style="left:883px;width:146px">
  <h4>Welcome</h4>
  <ul><li>Cloud Advisory Services</li><li>Email Everywhere</li><li>CRM Implementation</li></ul>
</div>
<div class="footer-base"></div>
<p class="copyright">Copyrights &copy; 2014. Vale Linebacker. All Rights Reserved.</p>
<span class="social" style="left:815px"></span>
<span class="social" style="left:852px"></span>
<span class="social" style="left:888px"></span>
<span class="social" style="left:925px"></span>
<span class="social" style="left:961px"></span>
<span class="social" style="left:998px"></span>

</body>
</html>
```